Employment Agency Website Design

We are working with an employment agency in California.

Some sites to use for content/competitors and inspiration:

https://www.pinecrestjobs.com/us/en
https://www.velmorusa.com
https://www.dravenworks.us
https://www.quillora.com/en
https://www.tomvalusa.com
https://www.fernstaffing.com

Thank you for taking the time to consider designing a website for us. We are web developers based in Stockton, CA, USA. Most of our projects go through the same process. Understanding this process may help you win a project with us. We custom-code all of our websites in-house. We don’t have any requirements as to what tools you use for your design, but we prefer Figma files. For any design that we label as four-stars, we send it to the client for review. The client picks the final design they want us to use. Once we complete this process, we will continue to show additional clients all the four-star sites and purchase them later. Your designs will have multiple chances to sell. For better chances of success, we ask that you follow these guidelines.

IMAGES:
If you use any images or icons in the design, we ask that you have a link to the asset so we can purchase the image/icon. Most of the designs we submit do not have the customer’s images on them unless they have some great images. Be creative; show us the feeling you are trying to portray with your image choices. Use any royalty-free site you choose. We subscribe to Adobe and mainly use their images, but we can purchase images outside of Adobe. PLEASE NOTE: we will not submit designs to clients with watermarks on the images.

FONTS:
We ask that you identify the fonts used in the design. This can be done in a message if you want. We typically use Google Fonts and Adobe Fonts.

CONTENT:
We're always open to different content and ideas. We often submit designs with stock images so the client can see our vision. We typically take pictures after the website launch to use their images with our vision. Lorem Ipsum is fine for paragraphs, but we ask that you write the headers in correct English. We want to be able to show the vision and identify the sections of the website.

INSPIRATION:
We typically add a couple of links in the brief of websites we like to help you get started in your design.

REVISIONS:
We do not often ask for revisions of the designs unless we see something in the design that may not appeal to the client. If there are slight changes that we want to make, we do that in the development process.

FEEDBACK:
We rarely give feedback on designs during the design process. We are working on many website projects and do not have the time to provide feedback. We usually respond if your request is well thought out and asks specific questions, but a note asking “feedback, please” usually goes unanswered.

```html
<!DOCTYPE html>
<html lang="en">
<head>
<meta charset="utf-8">
<title>Brightpath Talents — Landing Page Mobile View</title>
<link rel="stylesheet" href="https://fonts.googleapis.com/css2?family=Plus+Jakarta+Sans:wght@400;500;600;700;800&family=Lexend:wght@700;800&family=Barlow+Condensed:ital,wght@1,500&display=swap">
<style>
  :root {
    --red: #c8192e;
    --red-deep: #b0122a;
    --orange: #f0a21b;
    --ink: #111111;
    --muted: #6b6b6b;
    --frame: #3d3533;
    --panel: #efefef;
    --black: #0c0c0c;
    --white: #ffffff;
    --grad-a: #e8577d;
    --grad-b: #8e4fe0;
  }
  * { box-sizing: border-box; margin: 0; padding: 0; }
  html, body { width: 1200px; height: 1200px; overflow: hidden; background: var(--white); }
  body { font-family: "Plus Jakarta Sans", sans-serif; color: var(--ink); position: relative; }

  .board-title { position: absolute; left: 68px; top: 350px; font-family: "Lexend", sans-serif; font-weight: 800; font-size: 31px; line-height: 34px; color: var(--red); letter-spacing: .5px; }
  .board-subtitle { position: absolute; left: 68px; top: 440px; font-family: "Barlow Condensed", sans-serif; font-style: italic; font-weight: 500; font-size: 26px; line-height: 29px; color: #3a3a3a; letter-spacing: .5px; }

  .phone { position: absolute; width: 259px; border: 12px solid var(--frame); border-radius: 14px; overflow: hidden; background: var(--white); }
  .screen { width: 235px; position: relative; }

  /* shared */
  .brand { display: flex; align-items: center; gap: 4px; font-weight: 600; font-size: 14px; color: var(--red); }
  .brand-mark { width: 12px; height: 12px; background: var(--red); border-radius: 2px; }
  .btn-red { display: flex; align-items: center; justify-content: center; background: var(--red); color: var(--white); font-weight: 700; border-radius: 4px; }
  .section-title { text-align: center; font-weight: 700; font-size: 16px; }
  .shine-title { text-align: center; font-weight: 700; font-size: 26px; line-height: 32px; }
  .shine-title span, .resources-title span { color: var(--orange); }
  .body-text { text-align: center; font-size: 10.5px; line-height: 19px; color: #222; }
  .photo { background: linear-gradient(160deg, #d9d4cf, #a49a92 60%, #6e625c); }

  /* how it works */
  .how { background: var(--panel); }
  .steps { position: relative; width: 196px; height: 202px; margin: 0 auto; }
  .step { position: absolute; width: 86px; height: 86px; background: var(--white); border-radius: 5px; box-shadow: 0 2px 6px rgba(0,0,0,.12); padding: 9px 9px 0; }
  .step svg { width: 24px; height: 24px; display: block; margin-bottom: 8px; }
  .step p { font-size: 7.5px; line-height: 10px; color: #333; }
  .step-1 { left: 0; top: 0; } .step-2 { left: 110px; top: 0; }
  .step-3 { left: 0; top: 115px; } .step-4 { left: 110px; top: 115px; }
  .arrow { position: absolute; width: 0; height: 0; }
  .arrow-right { left: 94px; top: 38px; border-top: 6px solid transparent; border-bottom: 6px solid transparent; border-left: 9px solid var(--red); }
  .arrow-down { left: 147px; top: 95px; border-left: 6px solid transparent; border-right: 6px solid transparent; border-top: 9px solid var(--red); }
  .arrow-left { left: 94px; top: 153px; border-top: 6px solid transparent; border-bottom: 6px solid transparent; border-right: 9px solid var(--red); }

  /* footer */
  .footer { background: var(--black); color: var(--white); height: 264px; padding-top: 2px; }
  .footer .brand { justify-content: center; color: var(--white); font-size: 15px; margin-top: 22px; }
  .footer .brand-mark { background: var(--white); }
  .tagline { text-align: center; font-size: 6.5px; color: #ccc; margin-top: 2px; }
  .footer-links { display: grid; grid-template-columns: 1fr 1fr; padding: 26px 0 0 26px; row-gap: 8px; font-size: 9.5px; }
  .socials { display: flex; justify-content: center; gap: 10px; margin-top: 22px; }
  .socials span { width: 14px; height: 14px; border-radius: 50%; background: var(--white); }
  .copyright { text-align: center; font-size: 9px; margin-top: 14px; }

  /* home */
  .topbar { height: 50px; display: flex; align-items: center; justify-content: space-between; padding: 0 12px; background: var(--white); }
  .topbar .brand { font-size: 15px; }
  .topbar-action { width: 19px; height: 19px; background: var(--red); border-radius: 3px; display: flex; align-items: center; justify-content: center; }
  .hero { background: var(--panel); padding: 18px 14px 0; text-align: center; }
  .hero h1 { font-weight: 800; font-size: 30px; line-height: 42px; }
  .hero h1 .grad { background: linear-gradient(90deg, var(--grad-a), var(--grad-b)); -webkit-background-clip: text; background-clip: text; color: transparent; }
  .hero-text { font-size: 10.5px; line-height: 14px; margin: 22px 8px 0; }
  .search-card { background: var(--white); border-radius: 6px; box-shadow: 0 2px 8px rgba(0,0,0,.1); padding: 10px 9px; margin: 26px 0 0; text-align: left; }
  .field { height: 28px; border-radius: 3px; font-size: 9.5px; color: #999; display: flex; align-items: center; padding: 0 7px; margin-bottom: 8px; }
  .field-keyword { border: 1px solid var(--red); background: var(--white); }
  .field-location { background: #e2e2e2; border: 1px solid #d6d6d6; }
  .search-btn { height: 20px; font-size: 9.5px; font-weight: 500; gap: 5px; }
  .categories-title { padding: 48px 0 12px 14px; font-weight: 700; font-size: 17.5px; text-align: left; }
  .categories { background: var(--black); padding: 24px 14px 10px 26px; display: grid; grid-template-columns: 1fr 1fr; row-gap: 18px; height: 224px; }
  .category svg { width: 34px; height: 34px; display: block; margin-bottom: 8px; }
  .category h3 { color: var(--red); font-size: 11px; font-weight: 500; }
  .category small { display: block; color: #bbb; font-size: 7.5px; margin-top: 2px; }
  .explore-bar { height: 35px; background: var(--red); color: var(--white); display: flex; align-items: center; justify-content: space-between; padding: 0 14px 0 24px; font-size: 10px; font-weight: 600; }
  .explore-bar i { width: 20px; height: 20px; background: var(--white); border-radius: 50%; display: flex; align-items: center; justify-content: center; }
  .shine { padding: 28px 14px 0; }

  /* resources */
  .collage { position: relative; height: 204px; margin: 40px 0 0; }
  .resources-title { text-align: center; font-weight: 700; font-size: 24px; line-height: 32px; margin-top: 30px; }
  .stories { background: var(--panel); position: relative; height: 330px; margin-top: 38px; padding-top: 24px; }
  .quote-card { position: absolute; left: 28px; top: 76px; width: 178px; height: 186px; background: var(--white); border-radius: 6px; box-shadow: 0 2px 8px rgba(0,0,0,.12); padding: 14px 14px 0; }
  .quote-card blockquote { font-size: 12px; line-height: 15.5px; color: #333; }
  .author { display: flex; align-items: center; gap: 8px; margin-top: 18px; }
  .avatar { width: 28px; height: 28px; border-radius: 50%; background: linear-gradient(135deg, #cfc5bd, #7f726a); }
  .author b { display: block; font-size: 11px; font-weight: 600; }
  .author small { font-size: 7px; color: #555; }
  .peek { position: absolute; top: 76px; width: 10px; height: 186px; background: var(--white); box-shadow: 0 2px 8px rgba(0,0,0,.12); }
  .dots { position: absolute; top: 284px; left: 28px; display: flex; gap: 6px; }
  .dots span { width: 40px; height: 2px; background: #c4c4c4; }
  .dots span.on { background: #222; }
</style>
</head>
<body>

<h1 class="board-title">Brightpath<br>Talents</h1>
<p class="board-subtitle">Landing Page<br>Mobile View</p>

<svg width="0" height="0" style="position:absolute">
  <defs>
    <symbol id="i-find" viewBox="0 0 24 24"><g fill="none" stroke="#c8192e" stroke-width="2"><path d="M9 3h6v3H9z"/><path d="M15 4h3v8M9 4H5v17h7"/><circle cx="16" cy="17" r="3"/><path d="M18.2 19.2 21 22"/></g></symbol>
    <symbol id="i-scan" viewBox="0 0 24 24"><g fill="none" stroke="#c8192e" stroke-width="2"><path d="M5 10V3h10l4 4v3"/><path d="M2 13h20"/><path d="M5 16v5h14v-5"/></g></symbol>
    <symbol id="i-meet" viewBox="0 0 24 24"><g fill="none" stroke="#c8192e" stroke-width="2"><circle cx="8" cy="6" r="3"/><path d="M2 17c0-4 3-6 6-6s4 1 5 2"/><rect x="12" y="14" width="10" height="8" rx="1"/><path d="M15 14v-2h4v2"/></g></symbol>
    <symbol id="i-smile" viewBox="0 0 24 24"><g fill="none" stroke="#c8192e" stroke-width="2.2"><circle cx="12" cy="12" r="10"/><path d="M7.5 14c1.2 2 2.7 3 4.5 3s3.3-1 4.5-3"/><path d="M8.5 9v1M15.5 9v1"/></g></symbol>
  </defs>
</svg>

<!-- Footer screen -->
<div class="phone" style="left:347px; top:-24px; height:288px;">
  <div class="screen footer">
    <div class="brand"><span class="brand-mark"></span>brightpath talent</div>
    <p class="tagline">The future of work</p>
    <nav class="footer-links">
      <span>Find a Job</span><span>About Us</span>
      <span>Career Resources</span><span>Career with Us</span>
      <span>Career Insights</span><span>Location</span>
      <span>How to Apply</span><span>Investor Center</span>
    </nav>
    <div class="socials"><span></span><span></span><span></span><span></span></div>
    <p class="copyright">© Copyright 2024 Brightpath Talents Inc.</p>
  </div>
</div>

<!-- Home screen -->
<div class="phone" style="left:347px; top:294px; height:960px;">
  <div class="screen">
    <header class="topbar">
      <svg width="18" height="14" viewBox="0 0 18 14"><path d="M0 1h18M0 7h18M0 13h18" stroke="#c8192e" stroke-width="2"/></svg>
      <div class="brand"><span class="brand-mark"></span>brightpath talent</div>
      <span class="topbar-action"><svg width="9" height="9" viewBox="0 0 10 10"><path d="M5 8V2M2 5l3-3 3 3" stroke="#fff" stroke-width="1.6" fill="none"/></svg></span>
    </header>
    <section class="hero">
      <h1>Get Your<br><span class="grad">Dream Job</span><br>Today</h1>
      <p class="hero-text">Explore all the most exciting job roles based on your interest and study major.</p>
      <div class="search-card">
        <div class="field field-keyword">Job title or keyword</div>
        <div class="field field-location">Location or zip code</div>
        <div class="btn-red search-btn">Search Jobs
          <svg width="10" height="10" viewBox="0 0 12 12"><circle cx="5" cy="5" r="3.6" stroke="#fff" stroke-width="1.5" fill="none"/><path d="M7.7 7.7 11 11" stroke="#fff" stroke-width="1.5"/></svg>
        </div>
      </div>
      <h2 class="categories-title">Popular Categories ✨</h2>
    </section>
    <section class="categories">
      <div class="category">
        <svg viewBox="0 0 34 34"><g fill="none" stroke="#fff" stroke-width="2"><path d="M6 28 9 17 20 8l6 6-9 11z"/><path d="M6 28l7-7"/><circle cx="14.5" cy="19.5" r="2"/><path d="M20 8l3-3 6 6-3 3"/></g></svg>
        <h3>Designer</h3><small>341 Job Offers</small>
      </div>
      <div class="category">
        <svg viewBox="0 0 34 34"><g fill="none" stroke="#fff" stroke-width="2"><path d="M4 13h6l14-8v24l-14-8H4z"/><path d="M8 21l2 8h4l-2-8"/><path d="M28 13v8"/></g></svg>
        <h3>Marketer</h3><small>224 Job Offers</small>
      </div>
      <div class="category">
        <svg viewBox="0 0 34 34"><g fill="none" stroke="#fff" stroke-width="2"><path d="M16 6H5v24h24V18"/><path d="M26 3l5 5-13 13h-5v-5z"/></g></svg>
        <h3>Copywriter</h3><small>157 Job Offers</small>
      </div>
      <div class="category">
        <svg viewBox="0 0 34 34"><g fill="none" stroke="#fff" stroke-width="2"><path d="M3 10h7l3-4h8l3 4h7v19H3z"/><circle cx="17" cy="18" r="6"/></g></svg>
        <h3>Photographer</h3><small>267 Job Offers</small>
      </div>
    </section>
    <div class="explore-bar">EXPLORE ALL
      <i><svg width="10" height="10" viewBox="0 0 10 10"><path d="M2 8l6-6M3 2h5v5" stroke="#c8192e" stroke-width="1.6" fill="none"/></svg></i>
    </div>
    <section class="shine">
      <h2 class="shine-title">It’s Time For<br>You to <span>Shine</span></h2>
      <p class="body-text" style="margin-top:12px">We have thousands of jobs across the country. Whether you're looking for a remote job or a job near you.</p>
    </section>
  </div>
</div>

<!-- Shine screen -->
<div class="phone" style="left:624px; top:-12px; height:768px;">
  <div class="screen">
    <section style="padding:26px 14px 0">
      <h2 class="shine-title">It’s Time For<br>You to <span>Shine</span></h2>
      <p class="body-text" style="margin-top:18px">We have thousands of jobs across the country. Whether you're looking for a remote job or a job near you, <b>Brightpath Talent</b> is here to help you find the job that is right for you.</p>
      <div class="btn-red" style="width:150px;height:31px;margin:24px auto 0;font-size:9.5px;">Explore the Opportunities</div>
    </section>
    <div class="photo" role="img" aria-label="Smiling professional woman with arms crossed beside a recruiter assessment card" style="height:228px;margin-top:30px;position:relative;">
      <div style="position:absolute;right:6px;top:60px;text-align:right;font-size:6px;line-height:9px;color:#222;"><b style="font-size:11px;font-weight:500">Clara M.</b><br>Certified Public Accountant<br>10+ Years Experience<br>Fresno, CA</div>
    </div>
    <section class="how" style="height:260px;padding-top:34px;">
      <h2 class="section-title">How It Works 💼</h2>
      <div class="steps" style="margin-top:18px">
        <div class="step step-1"><svg><use href="#i-find"/></svg><p>Find your dream job in Brightpath Talent website</p></div>
        <span class="arrow arrow-right"></span>
        <div class="step step-2"><svg><use href="#i-scan"/></svg><p>Get your resume scanned by recruiters</p></div>
        <span class="arrow arrow-down"></span>
        <div class="step step-3"><svg><use href="#i-meet"/></svg><p>Get interviewed by your dream company</p></div>
        <span class="arrow arrow-left"></span>
        <div class="step step-4"><svg><use href="#i-smile"/></svg><p>Start your career ASAP by getting hired</p></div>
      </div>
    </section>
  </div>
</div>

<!-- How it works screen -->
<div class="phone" style="left:624px; top:786px; height:500px;">
  <div class="screen">
    <section class="how" style="height:328px;padding-top:32px;">
      <h2 class="section-title">How It Works 💼</h2>
      <div class="steps" style="margin-top:16px">
        <div class="step step-1"><svg><use href="#i-find"/></svg><p>Find your dream job in Brightpath Talent website</p></div>
        <span class="arrow arrow-right"></span>
        <div class="step step-2"><svg><use href="#i-scan"/></svg><p>Get your resume scanned by recruiters</p></div>
        <span class="arrow arrow-down"></span>
        <div class="step step-3"><svg><use href="#i-meet"/></svg><p>Get interviewed by your dream company</p></div>
        <span class="arrow arrow-left"></span>
        <div class="step step-4"><svg><use href="#i-smile"/></svg><p>Start your career ASAP by getting hired</p></div>
      </div>
    </section>
    <div class="photo" role="img" aria-label="Photo collage of people working at computers" style="width:112px;height:60px;margin:38px 0 0 18px;border-radius:3px;"></div>
  </div>
</div>

<!-- Resources and stories screen -->
<div class="phone" style="left:901px; top:-12px; height:1300px;">
  <div class="screen">
    <section class="how" style="height:314px;padding-top:19px;">
      <h2 class="section-title">How It Works 💼</h2>
      <div class="steps" style="margin-top:11px">
        <div class="step step-1"><svg><use href="#i-find"/></svg><p>Find your dream job in Brightpath Talent website</p></div>
        <span class="arrow arrow-right"></span>
        <div class="step step-2"><svg><use href="#i-scan"/></svg><p>Get your resume scanned by recruiters</p></div>
        <span class="arrow arrow-down"></span>
        <div class="step step-3"><svg><use href="#i-meet"/></svg><p>Get interviewed by your dream company</p></div>
        <span class="arrow arrow-left"></span>
        <div class="step step-4"><svg><use href="#i-smile"/></svg><p>Start your career ASAP by getting hired</p></div>
      </div>
    </section>
    <div class="collage">
      <div class="photo" role="img" aria-label="Collage of photos: woman coding at a desk, person at a laptop, man smiling at his computer, framed by a red outline" style="position:absolute;left:22px;top:0;width:190px;height:204px;border-radius:4px;background:linear-gradient(150deg,#3c4a52,#8a7a6c 45%,#c8192e 46%,#c8192e 48%,#b8aea4 49%,#5a5f66);"></div>
    </div>
    <h2 class="resources-title">Get <span>Valuable</span><br><span>Resources</span> Just<br>for You</h2>
    <p class="body-text" style="margin:20px 14px 0;font-size:10px;line-height:18.5px;">Make sure you are ready to work at your dream company with the best career provisions. Brightpath Talents has prepared valuable resources for you.</p>
    <div class="btn-red" style="width:150px;height:31px;margin:18px auto 0;font-size:9px;">Explore All Resources</div>
    <section class="stories">
      <h2 class="section-title">Explore Success Stories</h2>
      <span class="peek" style="left:-4px;border-radius:0 6px 6px 0"></span>
      <div class="quote-card">
        <blockquote>"Anyone searching knows how hard it is to find a position that aligns with your goals. They connected me with the perfect job."</blockquote>
        <div class="author">
          <span class="avatar" role="img" aria-label="Portrait of Maren Holt"></span>
          <div><b>Maren Holt</b><small>UI/UX Designer at Loomdesk</small></div>
        </div>
      </div>
      <span class="peek" style="right:-4px;border-radius:6px 0 0 6px"></span>
      <div class="dots"><span></span><span class="on"></span><span></span><span></span></div>
    </section>
    <div style="height:40px;background:var(--black)"></div>
  </div>
</div>

</body>
</html>
```